Day Spa Web Design Project

We just created a blog to add to our main site. We need the colors to match our main site and the look and feel of the blog to be smoother and less ameture looking, like the examples below.

Main Site, match this color scheme:
http://www.verelladayspa.com/

The project site:
http://blog.verelladayspa.com/

Our industry leaders blog site is our comparative and examples of what we need:
http://blog.wellnooklist.com/
http://blog.purelathermjournal.com/
http://thekelotabathblog.com/ (i like the layout a lot)
http://www.kneadharbor.com/blog/

Requirements
Must have
• social sharing.
Responsive design (already has it just keep it)
appealing mobile front page

```html
<!DOCTYPE html>
<html lang="en">
<head>
<meta charset="utf-8">
<title>Verella Day Spa – Blog</title>
<link rel="stylesheet" href="https://fonts.googleapis.com/css2?family=Didact+Gothic&family=Arimo:wght@400&display=swap">
<style>
  :root {
    --header-black: #050302;
    --header-brown: #2a1a10;
    --page-peach: #f0d09c;
    --heading-brown: #5a2e12;
    --body-text: #6e5a44;
    --button-brown: #5b2a0c;
    --footer-dark: #1a100b;
    --footer-line: #3a2a20;
    --submit-orange: #9a4a12;
    --input-cream: #f6f3dc;
    --white: #ffffff;
  }
  * { box-sizing: border-box; margin: 0; padding: 0; }
  html, body { width: 802px; height: 1200px; overflow: hidden; }
  body {
    position: relative;
    background: var(--page-peach);
    font-family: "Arimo", Arial, sans-serif;
  }
  .site-header {
    position: absolute; left: 0; top: 0; width: 802px; height: 66px;
    background: linear-gradient(to bottom, var(--header-black) 70%, var(--header-brown));
  }
  .brand {
    position: absolute; left: 80px; top: 7px; color: var(--white);
    font-family: "Didact Gothic", sans-serif;
  }
  .brand-name { font-size: 27px; line-height: 30px; letter-spacing: 0.3px; }
  .brand-tagline { font-size: 12px; line-height: 14px; }
  .main-nav {
    position: absolute; right: 87px; top: 24px; display: flex; gap: 16px;
    font-family: "Didact Gothic", sans-serif; font-size: 10.5px; color: var(--white);
  }
  .hero {
    position: absolute; left: 0; top: 66px; width: 802px; height: 274px;
    background:
      radial-gradient(ellipse 120px 140px at 640px 140px, #f3d2b8 0%, rgba(243,210,184,0) 100%),
      radial-gradient(ellipse 180px 120px at 330px 220px, #a6cf3a 0%, rgba(166,207,58,0) 100%),
      linear-gradient(to right, #d9d9a8 0%, #cfe090 35%, #e7ecc8 60%, #eed7c2 80%, #f1ddd0 100%);
  }
  .hero-title {
    position: absolute; left: 78px; top: 92px;
    font-family: "Didact Gothic", sans-serif; font-size: 32px; line-height: 39px;
    color: #111; letter-spacing: 0.5px;
  }
  .hero-dots { position: absolute; left: 83px; top: 255px; display: flex; gap: 7px; }
  .hero-dots span { width: 7px; height: 7px; border-radius: 50%; background: #bdbdbd; }
  .hero-dots span.active { background: #222; }
  .breadcrumb {
    position: absolute; left: 83px; top: 354px; font-size: 8.5px; color: #222;
  }
  .search {
    position: absolute; left: 560px; top: 346px; width: 160px; height: 21px;
    background: var(--white); border: 1px solid #e8dcc4;
  }
  .search svg { position: absolute; right: 6px; top: 5px; }
  .divider {
    position: absolute; left: 80px; top: 374px; width: 640px;
    border-top: 1px dashed #d7b889;
  }
  .post { position: absolute; width: 187px; text-align: center; }
  .post-image { position: relative; width: 187px; height: 173px; }
  .share-bar {
    position: absolute; left: 0; top: 0; width: 187px; height: 22px;
    background: #f2f2f2; display: flex; align-items: center; gap: 4px; padding: 0 4px;
  }
  .share-bar span {
    font-size: 7px; color: #333; background: var(--white); border: 1px solid #cfcfcf;
    border-radius: 2px; padding: 1px 4px;
  }
  .comment-count {
    position: absolute; left: 4px; bottom: 4px; font-size: 8px; font-style: italic; color: var(--white);
  }
  .post-title {
    margin-top: 12px; font-family: "Didact Gothic", sans-serif; font-size: 11.5px;
    color: var(--heading-brown); letter-spacing: 0.2px;
  }
  .post-excerpt {
    margin-top: 8px; font-size: 7.6px; line-height: 12px; color: var(--body-text);
    text-align: justify; text-align-last: center;
  }
  .read-more {
    display: inline-block; margin-top: 14px; width: 62px; height: 22px; line-height: 22px;
    background: var(--button-brown); color: var(--white); font-size: 8px;
  }
  .site-footer {
    position: absolute; left: 0; top: 1078px; width: 802px; height: 122px; background: var(--footer-dark);
  }
  .follow-label {
    position: absolute; left: 112px; top: 20px; color: var(--white);
    font-family: "Didact Gothic", sans-serif; font-size: 14.5px; letter-spacing: 0.3px;
  }
  .email-input {
    position: absolute; left: 274px; top: 17px; width: 186px; height: 22px; background: var(--input-cream);
  }
  .submit-button {
    position: absolute; left: 466px; top: 17px; width: 60px; height: 22px; line-height: 22px;
    background: var(--submit-orange); color: var(--white); font-size: 9px; text-align: center;
  }
  .footer-separator { position: absolute; left: 539px; top: 12px; height: 34px; border-left: 1px solid var(--footer-line); }
  .social-links { position: absolute; left: 552px; top: 17px; display: flex; gap: 3px; }
  .social-links span { width: 20px; height: 20px; border-radius: 50%; background: var(--white); }
  .footer-rule { position: absolute; left: 80px; top: 60px; width: 640px; border-top: 1px solid var(--footer-line); }
  .copyright {
    position: absolute; left: 0; width: 802px; top: 87px; text-align: center;
    color: var(--white); font-size: 8px; letter-spacing: 0.2px;
  }
</style>
</head>
<body>
  <header class="site-header">
    <div class="brand">
      <div class="brand-name">Verella Day Spa</div>
      <div class="brand-tagline">Natural Treatments for Body, Skin &amp; Nails</div>
    </div>
    <nav class="main-nav">
      <span>HOME</span><span>|</span><span>ABOUT US</span><span>|</span><span>CONTACT</span>
    </nav>
  </header>

  <section class="hero" role="img" aria-label="Spa photo with green candles, chrysanthemums, a cream jar and a smiling woman holding a flower">
    <h1 class="hero-title">NATURAL TREATMENTS FOR<br>BODY, SKIN &amp; NAILS</h1>
    <div class="hero-dots"><span class="active"></span><span></span><span></span></div>
  </section>

  <div class="breadcrumb">HOME</div>
  <div class="search">
    <svg width="10" height="10" viewBox="0 0 10 10"><circle cx="4" cy="4" r="3" fill="none" stroke="#ccc" stroke-width="1.2"/><line x1="6.2" y1="6.2" x2="9" y2="9" stroke="#ccc" stroke-width="1.4"/></svg>
  </div>
  <div class="divider"></div>

  <article class="post" style="left:80px; top:390px;">
    <div class="post-image" role="img" aria-label="Woman relaxing during a back massage" style="background:linear-gradient(160deg,#8a7a80 0%,#d8c7bd 45%,#e9e6e6 100%);">
      <div class="share-bar"><span>Like</span><span>Tweet</span><span>+1</span><span>Share</span></div>
      <div class="comment-count">Comment (4)</div>
    </div>
    <h2 class="post-title">KEYS TO STRESS REDUCTION</h2>
    <p class="post-excerpt">Some stress is natural, but often times stress becomes a problem when it leaves you feeling over-whelmed and out of control. Seventy seven percent of Americans report experiencing physical symptoms of stress, according to a 2012 study done by the Amerinor Wellness Association.</p>
    <span class="read-more">Read More</span>
  </article>

  <article class="post" style="left:307px; top:390px;">
    <div class="post-image" role="img" aria-label="Three runway models in colourful spring dresses" style="background:linear-gradient(to right,#e86a3a 0%,#f0b040 30%,#e8d8a0 50%,#c8b090 65%,#e090c0 85%,#7a9aa0 100%);"></div>
    <h2 class="post-title">WEARABLE SPRING TRENDS</h2>
    <p class="post-excerpt">Some stress is natural, but often times stress becomes a problem when it leaves you feeling over-whelmed and out of control. Seventy seven percent of Americans report experiencing physical symptoms of stress, according to a 2012 study done by the Amerinor Wellness Association.</p>
    <span class="read-more">Read More</span>
  </article>

  <article class="post" style="left:534px; top:390px;">
    <div class="post-image" role="img" aria-label="Woman resting on a massage table" style="background:linear-gradient(170deg,#c9d7dc 0%,#d9b99a 50%,#e8eef0 100%);"></div>
    <h2 class="post-title">KEYS TO STRESS REDUCTION</h2>
    <p class="post-excerpt">Some stress is natural, but often times stress becomes a problem when it leaves you feeling over-whelmed and out of control. Seventy seven percent of Americans report experiencing physical symptoms of stress, according to a 2012 study done by the Amerinor Wellness Association.</p>
    <span class="read-more">Read More</span>
  </article>

  <article class="post" style="left:80px; top:725px;">
    <div class="post-image" role="img" aria-label="Woman resting on a towel with orchids" style="background:linear-gradient(170deg,#6a9a9a 0%,#d9b090 40%,#f2f2f2 70%,#3a6aa8 100%);"></div>
    <h2 class="post-title">KEYS TO STRESS REDUCTION</h2>
    <p class="post-excerpt">Some stress is natural, but often times stress becomes a problem when it leaves you feeling over-whelmed and out of control. Seventy seven percent of Americans report experiencing physical symptoms of stress, according to a 2012 study done by the Amerinor Wellness Association.</p>
    <span class="read-more">Read More</span>
  </article>

  <article class="post" style="left:307px; top:725px;">
    <div class="post-image" role="img" aria-label="Candles, rolled towel and yellow orchids" style="background:linear-gradient(160deg,#e8e0b0 0%,#f4f0e0 45%,#ece6d6 100%);"></div>
    <h2 class="post-title">KEYS TO STRESS REDUCTION</h2>
    <p class="post-excerpt">Some stress is natural, but often times stress becomes a problem when it leaves you feeling over-whelmed and out of control. Seventy seven percent of Americans report experiencing physical symptoms of stress, according to a 2012 study done by the Amerinor Wellness Association.</p>
    <span class="read-more">Read More</span>
  </article>

  <article class="post" style="left:534px; top:725px;">
    <div class="post-image" role="img" aria-label="Woman relaxing outdoors beside spa stones and greenery" style="background:linear-gradient(120deg,#3a5a20 0%,#7a9a40 40%,#d8b89a 70%,#efe6da 100%);"></div>
    <h2 class="post-title">KEYS TO STRESS REDUCTION</h2>
    <p class="post-excerpt">Some stress is natural, but often times stress becomes a problem when it leaves you feeling over-whelmed and out of control. Seventy seven percent of Americans report experiencing physical symptoms of stress, according to a 2012 study done by the Amerinor Wellness Association.</p>
    <span class="read-more">Read More</span>
  </article>

  <footer class="site-footer">
    <div class="follow-label">FOLLOW US VIA EMAIL</div>
    <div class="email-input"></div>
    <div class="submit-button">SUBMIT</div>
    <div class="footer-separator"></div>
    <div class="social-links" aria-label="Social links"><span></span><span></span><span></span><span></span><span></span><span></span></div>
    <div class="footer-rule"></div>
    <div class="copyright">© 2013 - VERELLA DAY SPA – TIPS N' TRICKS</div>
  </footer>
</body>
</html>
```